Maple Beacon Website

We are starting a marketing company and to do that we need a website! We want a website that will inspire and persuade to bring out the awesomeness in our clients.
What we want to see:
- Inspirational and persuasive imagery that relate to Branding.
- No cliche images eg. business man, suits and hand shakes
- We want to transform and educate our clients.
- We want to show them the path and would like our website to really act as a guide that guides them step by step through our process.
- We want the portray that we are an investment but not have a pretentious way to it. We put our heart into every project and that is how we treat our clients.
-When you submit your design please include what platform you have created for. Preference would be Wordpress or Joobla.

We have included the psd file for the wire frame, logo files, font files, site map and a link to a video we create to give you more information on what we would like to see. http://clipvault.example/t/qk82LmZpr

Feel free to make small modification to the logos if you think it will improve it. Your creativity and advice is most welcome.
Updates

One thing we forgot. We would like to have our contact information near the top of the website as well as at the bottom.  Here is out contact info:

Email: info@maplebeacon.example
Phone: 587-555-0142

Project Deadline Extended
Reason: As we are new with the platform and that we want to optimize our results, we decided to extend the deadline by 15 days. Thanks!

Target Market(s)

28-60, Male and Female, Oil field, Local Businesses, Dentists, Chiropractors, Hair salon, Construction/Renovation, Events etc

Industry/Entity Type

Investment

Requirements
Must have
• - 4 Inspirational and persuasive Imagery for the top portion of the website
- Must have a feel as if your not on a website an example of this is linked below.
http://www.artbidhub.example/design/402957/web-design-by-lena-torvik
Nice to have
• - Creative advice from you.
- Creative buttons for Get Free Quote and Subscribe buttons. Something out of the box that draws peoples attention. eg. a 'B' button. Just and example but still something related to branding.
Should not have
• No Cliches

```html
<!DOCTYPE html>
<html lang="en">
<head>
<meta charset="utf-8">
<title>Maple Beacon</title>
<link href="https://fonts.googleapis.com/css2?family=Open+Sans:wght@400;600;700;800&family=Signika:wght@600;700&display=swap" rel="stylesheet">
<style>
:root{
  --green:#8cc63f;
  --green-dark:#4a7f16;
  --text:#5a5a5a;
  --grey:#8e8e8e;
  --page:#f7f7f7;
  --footer-top:#8a8a8a;
  --footer-bottom:#3a3a3a;
  --white:#fff;
}
*{margin:0;padding:0;box-sizing:border-box}
html,body{width:1200px;height:977px;overflow:hidden}
body{position:relative;background:var(--page);font-family:'Open Sans',sans-serif;color:var(--text)}
.topbar{position:absolute;left:0;top:0;width:1200px;height:39px;
  background:repeating-linear-gradient(135deg,#8fc43a 0 2px,#85bb32 2px 4px);
  box-shadow:0 1px 3px rgba(0,0,0,.2)}
.contact-line{position:absolute;right:175px;display:flex;align-items:center;gap:6px;font-weight:600;white-space:nowrap}
.topbar .contact-line{top:9px;color:var(--white);font-size:16px}
.contact-line svg{width:14px;height:14px}
.sep{margin:0 4px}
.hero-art{position:absolute;left:378px;top:50px;width:780px;height:370px;
  background:radial-gradient(ellipse at 50% 45%,#e6e6e6 0,#f2f2f2 45%,var(--page) 75%)}
.tree{position:absolute;left:523px;top:94px;width:347px;height:316px;
  background:radial-gradient(ellipse at 50% 40%,#9c9c9c 0,#b5b5b5 50%,rgba(200,200,200,0) 72%)}
.sidebar{position:absolute;left:171px;top:75px;width:205px;height:339px;
  background:linear-gradient(#f3f3f3,#e9e9e9);box-shadow:0 1px 5px rgba(0,0,0,.25)}
.logo{height:102px;display:flex;align-items:center;justify-content:center}
.logo-name{display:flex;align-items:center;gap:8px;font-weight:800;font-size:20px;color:var(--grey);white-space:nowrap}
.logo-name i{width:11px;height:11px;border-radius:50%;background:var(--green)}
.nav a{display:block;height:33.5px;line-height:33.5px;padding-left:14px;font-weight:700;font-size:14px;
  color:var(--green-dark);text-decoration:none;border-bottom:1px solid #fff;box-shadow:0 1px 0 #d4d4d4}
.connect{position:absolute;left:0;bottom:0;width:205px;height:65px;background:linear-gradient(#9a9a9a,#b8b8b8);
  color:var(--white);font-family:'Signika',sans-serif;font-weight:700;font-size:20px;line-height:20px;
  text-align:center;padding-top:13px}
.step{position:absolute;top:333px;width:82px;height:82px;border-radius:50%;
  background:linear-gradient(#9c9c9c,#7d7d7d);border:3px solid #d8d8d8;box-shadow:0 2px 4px rgba(0,0,0,.3);
  display:flex;align-items:center;justify-content:center;text-align:center;color:var(--white);
  font-weight:800;font-size:12.5px;line-height:15px}
.step.active{background:linear-gradient(#9fd54b,#6fae22)}
.rule{position:absolute;left:175px;width:848px;border-top:1px dashed #aaa}
.social{position:absolute;top:437px;width:45px;height:45px;background:linear-gradient(#555,#2b2b2b);border-radius:2px}
.tips{position:absolute;left:389px;top:440px}
.tips h3{font-weight:700;font-size:21px;color:var(--green);line-height:24px}
.tips p{font-weight:700;font-size:15.5px;color:#555;line-height:18px}
.email-field{position:absolute;left:620px;top:443px;width:301px;height:37px;border:1px solid #ccc;background:#fff;
  font-size:13px;color:#777;padding:10px 8px}
.btn-subscribe{position:absolute;left:927px;top:443px;width:100px;height:36px;border:1px solid #999;
  background:linear-gradient(#c9c9c9,#8f8f8f);color:var(--white);font-weight:700;font-size:15px;
  display:flex;align-items:center;justify-content:center}
.welcome{position:absolute;left:174px;top:508px;font-family:'Signika',sans-serif;font-weight:700;font-size:22px;color:#2a2a2a}
.content{position:absolute;left:176px;top:547px;width:830px;font-size:13.7px;line-height:19px}
.content h4{color:var(--green-dark);font-size:14.5px;font-weight:700;line-height:19px}
.checks{list-style:none;margin-top:7px}
.checks li{display:flex;align-items:center;gap:10px;height:31px;color:#444}
.checks svg{width:17px;height:17px;margin-left:1px}
.closing{margin-top:16px}
.btn-quote{position:absolute;left:884px;top:733px;width:141px;height:36px;border-radius:2px;
  background:linear-gradient(#6fb22a,#3f7f12);border:1px solid #3a6e12;color:var(--white);
  font-weight:700;font-size:15px;display:flex;align-items:center;justify-content:center}
.footer{position:absolute;left:0;top:869px;width:1200px;height:108px;background:linear-gradient(var(--footer-top),var(--footer-bottom))}
.footer-nav{position:absolute;left:174px;top:27px;display:flex;gap:12px;font-size:15.5px;color:var(--white);font-weight:600}
.copyright{position:absolute;left:174px;top:53px;font-size:15px;color:var(--green)}
.footer .contact-line{top:28px;color:var(--white);font-size:16px;font-weight:400}
.footer .contact-line b{font-weight:700}
</style>
</head>
<body>
<header class="topbar">
  <div class="contact-line">
    <svg viewBox="0 0 14 14"><rect x="1" y="3" width="12" height="8" fill="#333"/><path d="M1 3l6 5 6-5" stroke="#fff" fill="none"/></svg>
    info@maplebeacon.example <span class="sep">|</span>
    <svg viewBox="0 0 14 14"><path d="M3 1l3 3-1.5 1.5c1 2 2 3 4 4L10 8l3 3-2 2C6 12 2 8 1 3z" fill="#222"/></svg>
    587-555-0142
  </div>
</header>

<div class="hero-art"></div>
<div class="tree" role="img" aria-label="Illustration of a grey tree with one bright green leaf"></div>

<aside class="sidebar">
  <div class="logo">
    <div class="logo-name"><i></i>MAPLE BEACON</div>
  </div>
  <nav class="nav">
    <a>STRATEGY</a><a>PORTFOLIO</a><a>ABOUT US</a><a>CONTACT US</a><a>BLOG</a>
  </nav>
  <div class="connect">CONNECT<br>WITH US</div>
</aside>

<div class="step active" style="left:453px">MAPLE<br>BEACON</div>
<div class="step" style="left:591px">BE<br>FOUND</div>
<div class="step" style="left:728px">CONNECT</div>
<div class="step" style="left:866px">GET<br>GROWING</div>

<div class="rule" style="top:428px"></div>
<div class="social" style="left:171px" aria-label="Social profile"></div>
<div class="social" style="left:224px" aria-label="Social profile"></div>
<div class="social" style="left:276px" aria-label="Social profile"></div>
<div class="social" style="left:329px" aria-label="Blog"></div>
<div class="tips">
  <h3>GET TIPS AND TRICKS!</h3>
  <p>Subscribe to our Newsletter.</p>
</div>
<div class="email-field">your email id</div>
<div class="btn-subscribe">Subscribe</div>
<div class="rule" style="top:495px"></div>

<h2 class="welcome">WELCOME TO MAPLE BEACON</h2>
<main class="content">
  <h4>Our Mission</h4>
  <p>Etiam adipiscing mollis nulla, ac bibendum elit commodo ac. Pellentesque vehicula sodales vulputate. Suspendisse vel semper tortor. Duis tristique pharetra ligula sed bibendum. Etiam adipiscing mollis nulla, ac bibendum elit commodo ac. Etiam adipiscing mollis nulla, ac bibendum elit commodo ac.</p>
  <ul class="checks">
    <li><svg viewBox="0 0 17 17"><rect width="17" height="17" rx="3" fill="#8cc63f"/><path d="M4 9l3 3 6-7" stroke="#fff" stroke-width="2.2" fill="none"/></svg>Nam ac risus metus, sit amet blandit ante.</li>
    <li><svg viewBox="0 0 17 17"><rect width="17" height="17" rx="3" fill="#8cc63f"/><path d="M4 9l3 3 6-7" stroke="#fff" stroke-width="2.2" fill="none"/></svg>Nunc adipiscing, ipsum eu scelerisque euismod, diam nisl condimentum neque,</li>
    <li><svg viewBox="0 0 17 17"><rect width="17" height="17" rx="3" fill="#8cc63f"/><path d="M4 9l3 3 6-7" stroke="#fff" stroke-width="2.2" fill="none"/></svg>Vel gravida ligula velit vitae nisl. Pellentesque at dignissim ipsum. Vivamus id massa arcu.</li>
    <li><svg viewBox="0 0 17 17"><rect width="17" height="17" rx="3" fill="#8cc63f"/><path d="M4 9l3 3 6-7" stroke="#fff" stroke-width="2.2" fill="none"/></svg>Phasellus feugiat condimentum neque ac bibendum.</li>
    <li><svg viewBox="0 0 17 17"><rect width="17" height="17" rx="3" fill="#8cc63f"/><path d="M4 9l3 3 6-7" stroke="#fff" stroke-width="2.2" fill="none"/></svg>Pellentesque dictum lectus sapien, eu pulvinar eros.</li>
  </ul>
  <p class="closing">Maecenas lacinia, nulla at interdum dapibus, velit sapien posuere eros, et hendrerit purus erat quis est. Proin commodo blandit mauris sed convallis. Donec tellus metus, feugiat sed condimentum congue, dignissim ut leo.</p>
</main>
<div class="btn-quote">Get a Free Quote!</div>

<footer class="footer">
  <nav class="footer-nav"><span>Site Map</span><span>Strategy</span><span>Portfolio</span><span>About Us</span><span>Contact Us</span><span>Blog</span></nav>
  <div class="copyright">©MAPLE BEACON INC. 2013</div>
  <div class="contact-line">
    <svg viewBox="0 0 14 14"><rect x="1" y="3" width="12" height="8" fill="#eee"/><path d="M1 3l6 5 6-5" stroke="#666" fill="none"/></svg>
    info@maplebeacon.example <span class="sep">|</span>
    <svg viewBox="0 0 14 14"><path d="M3 1l3 3-1.5 1.5c1 2 2 3 4 4L10 8l3 3-2 2C6 12 2 8 1 3z" fill="#111"/></svg>
    <b>587-555-0142</b>
  </div>
</footer>
</body>
</html>
```